Non Profit Company Looking For New Website

The website for Fernvale Quillstone Heritage Society should offer the viewer beautiful photos that inspire condifence and joy and tap into our love of horses.

We would like to see a website that displays trust, quality and confidence. Needs to be responsive and mobile friendly for all browsers and coded for both Android & IOS.

READ ATTACHED WEBSITE TEMPLATE FOR COMPLETE DETAILS ON WHAT WE ARE LOOKING FOR.

Looking for recommmendations if we should use WordPress/WooCommerce for site or Wordpress with Shopify Plug in or just Shopify.

Must be both desktop and mobile friendly with fast page load speed. Need the ability to edit ourselves.

Industry/Entity Type

Non Profit

Coding

Coded - Design and coding required

Number of Pages Required

5+ page

Requirements
Must have
• We would like to see a website that displays trust, quality and confidence. Needs to be responsive and mobile friendly for all browsers and coded for both Android & IOS.

Looking for recommendations if we should use WordPress/WooCommerce for site or Wordpress with Shopify Plug in or just Shopify.

Logo Colour:
Pantone 7621 C

READ TEMPLATE THAT IS ATTACHED
Nice to have
• Like look of this website as a sample:
https://www.quellbrimtorva.com/

Another similar non profit organization
https://pellaworthcindle.com/

```html
<!DOCTYPE html>
<html lang="en">
<head>
<meta charset="utf-8">
<title>Fernvale Quillstone Heritage Society</title>
<link href="https://fonts.googleapis.com/css2?family=Playfair+Display:ital,wght@0,400;0,500;1,500&family=Mulish:wght@400;600&display=swap" rel="stylesheet">
<style>
:root{
  --red:#c01f2c;
  --red-deep:#a81a26;
  --ink:#222;
  --muted:#444;
  --white:#fff;
  --black:#000;
  --serif:'Playfair Display', Georgia, serif;
  --sans:'Mulish', Arial, sans-serif;
}
*{box-sizing:border-box;margin:0;padding:0}
html,body{width:1200px;height:3750px;overflow:hidden}
body{position:relative;font-family:var(--sans);color:var(--ink);background:var(--white)}
.abs{position:absolute}
.btn{position:absolute;background:var(--white);color:#222;font-family:var(--serif);font-size:16px;letter-spacing:.5px;display:flex;align-items:center;justify-content:center;border-radius:2px}

/* header */
.site-header{position:absolute;left:0;top:0;width:1200px;height:110px;background:var(--white)}
.brand{position:absolute;left:168px;top:26px;display:flex;align-items:center;gap:10px;color:var(--red);font-family:var(--serif);font-size:14px;line-height:19px;letter-spacing:1px}
.brand-mark{width:26px;height:26px;background:var(--red);flex:none}
.main-nav{position:absolute;right:155px;top:38px;display:flex;gap:40px;font-size:13px;font-weight:600;letter-spacing:.5px}
.main-nav a{color:#333;text-decoration:none}
.main-nav a.active{color:var(--red)}

/* hero */
.hero{position:absolute;left:0;top:110px;width:1200px;height:526px;
  background:
    radial-gradient(ellipse 180px 240px at 800px 60px,rgba(230,220,215,.35),transparent 70%),
    radial-gradient(ellipse 300px 170px at 800px 330px,#3a1f16,transparent 75%),
    linear-gradient(90deg,#0c0c0c 0%,#1e1a18 40%,#4a3025 62%,#7a5648 82%,#a88676 100%)}
.hero-text{position:absolute;left:156px;top:125px;color:var(--white);font-family:var(--serif)}
.hero-text .l1{font-size:36px;line-height:44px}
.hero-text .l2{font-size:48px;color:var(--red);line-height:56px}
.hero-text .l3{font-size:28px;line-height:38px}

/* intro */
.intro-art{left:405px;top:650px;width:390px;height:335px;
  background:
    radial-gradient(ellipse 70px 110px at 95px 110px,#d8d4d0,transparent 75%),
    radial-gradient(ellipse 80px 110px at 235px 130px,#3a2a26,transparent 75%),
    linear-gradient(180deg,#f3efee,#f7f3f2)}
.tagline{left:0;width:1200px;top:858px;text-align:center;font-family:var(--serif);font-style:italic;color:var(--red);font-size:34px;font-weight:500}
.intro-copy{left:0;width:1200px;top:1005px;text-align:center;font-size:20px;line-height:34px;color:var(--muted)}

/* aftercare */
.aftercare{left:0;top:1102px;width:1200px;height:478px;background:linear-gradient(180deg,#c42630,#b81e29)}
.section-title{font-family:var(--serif);font-weight:400;color:var(--white)}
.aftercare h2{position:absolute;left:158px;top:102px;font-size:34px;line-height:42px}
.aftercare p{position:absolute;left:158px;top:204px;width:410px;color:var(--white);font-size:16px;line-height:26px}
.aftercare-photo{left:662px;top:55px;width:382px;height:382px;border-radius:50%;border:4px solid #3b2a25;
  background:
    radial-gradient(ellipse 110px 170px at 140px 190px,#3e2418,transparent 80%),
    radial-gradient(ellipse 110px 180px at 270px 150px,#4a3020,transparent 80%),
    linear-gradient(180deg,#b9c08a,#8a9a55 70%,#6a7a40)}

/* adopt */
.adopt{left:0;top:1580px;width:1200px;height:668px;background:linear-gradient(180deg,#2e2e2e,#1d1d1d)}
.adopt h2{position:absolute;width:1200px;text-align:center;top:88px;font-size:34px}
.adopt p{position:absolute;width:1200px;text-align:center;top:146px;color:var(--white);font-size:15px;line-height:27px}
.adopt-card{position:absolute;top:230px;width:284px;height:265px;border:2px solid var(--red)}
.adopt-card.one{left:158px;background:radial-gradient(ellipse 90px 70px at 150px 130px,#3a2418,transparent 80%),linear-gradient(180deg,#d9dccf 0%,#7c8c52 45%,#c9c3b2 75%,#e0d8c8)}
.adopt-card.two{left:458px;background:radial-gradient(ellipse 100px 75px at 140px 120px,#3c2214,transparent 80%),linear-gradient(180deg,#e2e4e0 0%,#b8b4ac 40%,#a9a39a 100%)}
.adopt-card.three{left:759px;background:radial-gradient(ellipse 100px 60px at 150px 110px,#4a2e1e,transparent 80%),linear-gradient(180deg,#e4e6dc 0%,#b9b99a 30%,#8fb03e 60%,#a3c245)}

/* horses */
.horses-photo{left:158px;top:2306px;width:734px;height:520px;
  background:
    radial-gradient(ellipse 170px 260px at 230px 300px,#3a1d12,transparent 80%),
    linear-gradient(90deg,#6f7d86,#8a8278 30%,#6a5a4a 60%,#4a3a30)}
.horses-panel{left:538px;top:2378px;width:504px;height:374px;background:var(--red)}
.horses-panel h2{position:absolute;left:65px;top:85px;font-size:32px}
.horses-panel p{position:absolute;left:65px;top:143px;width:400px;color:var(--white);font-size:15px;line-height:26px}

/* contact */
.contact{left:0;top:2862px;width:1200px;height:478px;background:linear-gradient(180deg,#c52731,#b71d28)}
.contact h2{position:absolute;width:1200px;text-align:center;top:52px;font-size:32px}
.info{position:absolute;left:158px;display:flex;gap:15px;color:var(--white)}
.info .icon{width:60px;height:60px;border:2px solid var(--white);border-radius:50%;display:flex;align-items:center;justify-content:center;flex:none}
.info h3{font-size:15px;font-weight:600;letter-spacing:.5px;margin-top:6px}
.info span{font-size:13px;line-height:20px;display:block}
.field{position:absolute;background:var(--white);font-size:14px;color:#444;padding:12px 15px;border-radius:2px}
.captcha{position:absolute;left:532px;top:386px;width:190px;height:52px;background:#f9f9f9;border:1px solid #ddd;display:flex;align-items:center;gap:8px;padding:0 10px;font-size:10px;color:#333}
.captcha .box{width:16px;height:16px;border:2px solid #c1c1c1;background:#fff}
.captcha .badge{width:26px;height:26px;background:#9aa8c8;margin-left:auto;border-radius:3px}

/* footer */
.site-footer{left:0;top:3340px;width:1200px;height:410px;background:var(--black);color:var(--white)}
.footer-brand{position:absolute;left:150px;top:135px;width:150px;text-align:center;color:var(--red);font-family:var(--serif);font-size:16px;line-height:22px;letter-spacing:1px}
.footer-col{position:absolute;top:88px;font-size:13px;line-height:20px}
.footer-col h4{font-family:var(--serif);font-weight:400;font-size:15px;letter-spacing:.5px;margin-bottom:14px}
.footer-col li{list-style:none;margin-bottom:11px}
.footer-col .loc{color:var(--red);margin-bottom:4px}
.sub-input{width:210px;height:36px;background:var(--white);color:#333;font-size:13px;display:flex;align-items:center;justify-content:center;border-radius:2px}
.sub-btn{width:210px;height:36px;background:var(--red);font-family:var(--serif);font-size:15px;display:flex;align-items:center;justify-content:center;margin-top:8px;border-radius:2px}
.socials{display:flex;gap:9px;margin-top:26px}
.socials i{width:24px;height:24px;border-radius:50%;background:var(--white);display:block}
.copyright{position:absolute;width:1200px;text-align:center;top:370px;font-size:11px;color:#bbb}
.copyright em{font-style:normal;color:var(--red)}
</style>
</head>
<body>

<header class="site-header">
  <div class="brand"><div class="brand-mark"></div><div>FERNVALE<br>QUILLSTONE<br>HERITAGE</div></div>
  <nav class="main-nav">
    <a class="active" href="#">HOME</a><a href="#">ABOUT</a><a href="#">ADOPT</a><a href="#">HORSES</a><a href="#">DONATE / SHOP</a><a href="#">CONTACT</a>
  </nav>
</header>

<section class="hero" role="img" aria-label="Photo: rider in a white top on a dark bay horse in an indoor arena">
  <div class="hero-text">
    <div class="l1">We Support</div>
    <div class="l2">And Develop</div>
    <div class="l3">Retired thoroughbred<br>racehorses for their next<br>chapter in life</div>
  </div>
  <div class="btn" style="left:160px;top:358px;width:196px;height:44px">VIEW HORSES</div>
</section>

<div class="abs intro-art" role="img" aria-label="Photo: grey horse and a rider in a helmet standing together"></div>
<div class="abs tagline">Retire.&nbsp; Retrain.&nbsp; Rehome.</div>
<p class="abs intro-copy">Fernvale Quillstone Heritage Society (FQHS) is a registered<br>not-for-profit organization in Fernvale.</p>

<section class="abs aftercare">
  <h2 class="section-title">What is Thoroughbred<br>Aftercare?</h2>
  <p>The health, safety and welfare of our equine athletes does not end at the finish line, and retirement and aftercare are critical to the success of the racing industry.</p>
  <div class="btn" style="left:158px;top:335px;width:225px;height:43px">LEARN MORE ABOUT US</div>
  <div class="abs aftercare-photo" role="img" aria-label="Photo: woman resting her head against a bay horse in a green field"></div>
</section>

<section class="abs adopt">
  <h2 class="section-title">Adopt a Horse</h2>
  <p>Fernvale Quillstone Heritage is committed to<br>helping match you with the perfect horse.</p>
  <div class="adopt-card one" role="img" aria-label="Photo: bay horse trotting through shallow water"></div>
  <div class="adopt-card two" role="img" aria-label="Photo: bay horse standing in a sand paddock"></div>
  <div class="adopt-card three" role="img" aria-label="Photo: bay horse standing in a green field"></div>
  <div class="btn" style="left:487px;top:527px;width:226px;height:43px">ADOPT NOW</div>
</section>

<div class="abs horses-photo" role="img" aria-label="Photo: bay horse with a white star wearing a red halter"></div>
<section class="abs horses-panel">
  <h2 class="section-title">Horses</h2>
  <p>Many desktop publishing packages and web page editors now use Lorem Ipsum as their default model text, and a search for 'lorem ipsum'</p>
  <div class="btn" style="left:65px;top:240px;width:213px;height:44px">MORE WAYS TO GIVE</div>
</section>

<section class="abs contact">
  <h2 class="section-title">Have A Question Or Need More Information</h2>
  <div class="info" style="top:128px">
    <div class="icon"><svg width="24" height="28" viewBox="0 0 24 28"><path d="M12 1C6.5 1 3 5 3 10c0 7 9 17 9 17s9-10 9-17c0-5-3.5-9-9-9z" fill="#fff"/><circle cx="12" cy="10" r="3.5" fill="#c01f2c"/></svg></div>
    <div><h3>LOCATION</h3><span>Lorem Ipsum is simply<br>Dummy text P.O. Box 156</span></div>
  </div>
  <div class="info" style="top:230px">
    <div class="icon"><svg width="26" height="26" viewBox="0 0 24 24"><path d="M6.6 10.8a15 15 0 0 0 6.6 6.6l2.2-2.2a1 1 0 0 1 1-.25 11.4 11.4 0 0 0 3.6.57 1 1 0 0 1 1 1V20a1 1 0 0 1-1 1A17 17 0 0 1 3 4a1 1 0 0 1 1-1h3.5a1 1 0 0 1 1 1c0 1.25.2 2.45.57 3.57a1 1 0 0 1-.25 1z" fill="#fff"/></svg></div>
    <div><h3>CALL US</h3><span>123-456-789</span></div>
  </div>
  <div class="info" style="top:332px">
    <div class="icon"><svg width="26" height="20" viewBox="0 0 26 20"><rect x="1" y="1" width="24" height="18" rx="2" fill="#fff"/><path d="M2 3l11 8 11-8" stroke="#c01f2c" stroke-width="2" fill="none"/></svg></div>
    <div><h3>MAIL US</h3><span>hello@fernvalequill.org</span></div>
  </div>
  <div class="field" style="left:532px;top:142px;width:249px;height:43px">First Name</div>
  <div class="field" style="left:793px;top:142px;width:249px;height:43px">Last Name</div>
  <div class="field" style="left:532px;top:194px;width:249px;height:43px">Phone</div>
  <div class="field" style="left:793px;top:194px;width:249px;height:43px">Email</div>
  <div class="field" style="left:532px;top:247px;width:510px;height:128px">How can we help&nbsp; you?</div>
  <div class="captcha"><div class="box"></div>I'm not a robot<div class="badge"></div></div>
  <div class="btn" style="left:728px;top:386px;width:174px;height:44px">SUBMIT NOW</div>
</section>

<footer class="abs site-footer">
  <div class="footer-brand">FERNVALE<br>QUILLSTONE<br>HERITAGE</div>
  <div class="footer-col" style="left:404px">
    <h4>QUICK LINK</h4>
    <ul><li>Home</li><li>About</li><li>Adopt</li><li>Horses</li><li>Donate / Shop</li><li>Contact</li></ul>
  </div>
  <div class="footer-col" style="left:600px">
    <h4>QUICK CONTACT</h4>
    <div class="loc">Location</div>
    <div>Lorem Ipsum is simply<br>Dummy text<br>P.O. Box 156</div>
    <div class="loc" style="margin-top:18px">Location</div>
    <div>Lorem Ipsum is simply<br>Dummy text<br>P.O. Box 156</div>
  </div>
  <div class="footer-col" style="left:832px">
    <h4>FOLLOW US</h4>
    <div class="sub-input">Enter Your Mail ID</div>
    <div class="sub-btn">Subscribe</div>
    <div class="socials"><i></i><i></i><i></i><i></i></div>
  </div>
  <div class="copyright">Copyright 2021 <em>Fernvale</em> All Right Reserved</div>
</footer>

</body>
</html>
```